Aunt Roula's Bakery

I am about to create a luxury boutique that specializes in cake baking and cupcake
and ready for parties and special events and order delivery
the logo has already made

Boutique

Email:auntroulasbakery@mailbox-example.net
Instagram: aunt_roula_bakery
Twitter: xxxxxxx
WhatsApp: xxxxxxx

Requirements
Must have
• luxury design

```html
<!DOCTYPE html>
<html lang="en">
<head>
<meta charset="utf-8">
<title>Aunt Roula's Bakery – Business Cards</title>
<link rel="stylesheet" href="https://fonts.googleapis.com/css2?family=Open+Sans:wght@400;600;700&display=swap">
<style>
  :root {
    --backdrop: #e9e9e7;
    --card-grey: #7b7a76;
    --band-white: #ebebeb;
    --rose: #d99fb1;
    --ink-grey: #6e6d69;
    --text-light: #ffffff;
  }
  * { margin: 0; padding: 0; box-sizing: border-box; }
  html, body { width: 1200px; height: 782px; overflow: hidden; background: var(--backdrop); }
  body { position: relative; font-family: "Open Sans", Arial, sans-serif; }

  .card {
    position: absolute;
    width: 326px;
    height: 570px;
    background: var(--card-grey);
    overflow: hidden;
    box-shadow: 0 6px 18px rgba(0,0,0,0.18);
  }
  .card--portrait { left: 710px; top: 84px; }
  .card--landscape { left: 686px; top: 340px; transform-origin: top left; transform: rotate(90deg) scale(0.965); }

  .card__name {
    position: absolute; left: 26px; top: 56px;
    color: var(--text-light); font-weight: 700; font-size: 22px; letter-spacing: 0.5px;
  }
  .card__role {
    position: absolute; left: 26px; top: 86px;
    color: var(--rose); font-weight: 600; font-size: 14px;
  }
  .card__rule { position: absolute; left: 88px; top: 92px; width: 238px; height: 10px; }

  .ornament { position: absolute; left: 0; width: 326px; }
  .ornament--top { top: 140px; height: 44px; background: linear-gradient(90deg, rgba(217,159,177,0.25), rgba(217,159,177,0.55), rgba(217,159,177,0.25)); }
  .ornament--bottom { top: 374px; height: 44px; background: linear-gradient(90deg, rgba(217,159,177,0.25), rgba(217,159,177,0.55), rgba(217,159,177,0.25)); }
  .ornament--footer { top: 510px; height: 60px; background: linear-gradient(180deg, rgba(139,138,134,0), rgba(139,138,134,0.7)); }

  .brand-band {
    position: absolute; left: 0; top: 189px; width: 326px; height: 183px;
    background: var(--band-white);
  }
  .brand-band__scroll {
    position: absolute; top: 30px; width: 72px; height: 30px;
    background: rgba(110,109,105,0.15);
  }
  .brand-band__scroll--left { left: 58px; }
  .brand-band__scroll--right { right: 58px; }
  .brand-band__dot {
    position: absolute; left: 141px; top: 10px; width: 44px; height: 44px;
    border-radius: 50%; background: var(--rose);
  }
  .brand-band__name {
    position: absolute; left: 0; width: 326px; text-align: center;
    color: var(--ink-grey); font-weight: 600; white-space: nowrap;
  }
  .brand-band__name--main { top: 70px; font-size: 27px; letter-spacing: 0.5px; }
  .brand-band__name--sub { top: 106px; font-size: 17px; letter-spacing: 6px; }
  .brand-band__ornament {
    position: absolute; left: 118px; top: 138px; width: 90px; height: 30px;
    background: rgba(110,109,105,0.15);
  }

  .contacts {
    position: absolute; left: 26px; top: 430px; list-style: none;
    color: var(--text-light); font-size: 15px; line-height: 20px;
  }
  .contacts li { display: flex; align-items: center; gap: 8px; white-space: nowrap; }
  .contacts__email { font-size: 13px; }
  .contacts__mark { width: 11px; height: 11px; border-radius: 50%; background: var(--rose); flex: none; }
  .contacts__icon { width: 12px; height: 10px; flex: none; }
</style>
</head>
<body>

<article class="card card--landscape">
  <h1 class="card__name">AUNT ROULA</h1>
  <p class="card__role">OWNER</p>
  <svg class="card__rule" viewBox="0 0 238 10"><path d="M0 7 H232 L236 3" fill="none" stroke="#d99fb1" stroke-width="2"/></svg>
  <div class="ornament ornament--top" role="img" aria-label="Pink scrolling flourish border"></div>
  <section class="brand-band">
    <div class="brand-band__scroll brand-band__scroll--left" role="img" aria-label="Grey wrought scroll ornament"></div>
    <div class="brand-band__scroll brand-band__scroll--right" role="img" aria-label="Grey wrought scroll ornament"></div>
    <span class="brand-band__dot"></span>
    <p class="brand-band__name brand-band__name--main">AUNT ROULA'S</p>
    <p class="brand-band__name brand-band__name--sub">BAKERY</p>
    <div class="brand-band__ornament" role="img" aria-label="Grey scroll flourish"></div>
  </section>
  <div class="ornament ornament--bottom" role="img" aria-label="Pink scrolling flourish border"></div>
  <ul class="contacts">
    <li><span class="contacts__mark"></span>xxxxxxx</li>
    <li><span class="contacts__mark"></span>xxxxxxx</li>
    <li><span class="contacts__mark"></span>aunt_roula_bakery</li>
    <li class="contacts__email"><svg class="contacts__icon" viewBox="0 0 12 10"><rect x="0.5" y="0.5" width="11" height="9" fill="none" stroke="#d99fb1"/><path d="M0.5 0.5 L6 5.5 L11.5 0.5" fill="none" stroke="#d99fb1"/></svg>auntroulasbakery@mailbox-example.net</li>
  </ul>
  <div class="ornament ornament--footer" role="img" aria-label="Faint grey swirl pattern"></div>
</article>

<article class="card card--portrait">
  <h2 class="card__name">AUNT ROULA</h2>
  <p class="card__role">OWNER</p>
  <svg class="card__rule" viewBox="0 0 238 10"><path d="M0 7 H232 L236 3" fill="none" stroke="#d99fb1" stroke-width="2"/></svg>
  <div class="ornament ornament--top" role="img" aria-label="Pink scrolling flourish border"></div>
  <section class="brand-band">
    <div class="brand-band__scroll brand-band__scroll--left" role="img" aria-label="Grey wrought scroll ornament"></div>
    <div class="brand-band__scroll brand-band__scroll--right" role="img" aria-label="Grey wrought scroll ornament"></div>
    <span class="brand-band__dot"></span>
    <p class="brand-band__name brand-band__name--main">AUNT ROULA'S</p>
    <p class="brand-band__name brand-band__name--sub">BAKERY</p>
    <div class="brand-band__ornament" role="img" aria-label="Grey scroll flourish"></div>
  </section>
  <div class="ornament ornament--bottom" role="img" aria-label="Pink scrolling flourish border"></div>
  <ul class="contacts">
    <li><span class="contacts__mark"></span>xxxxxxx</li>
    <li><span class="contacts__mark"></span>xxxxxxx</li>
    <li><span class="contacts__mark"></span>aunt_roula_bakery</li>
    <li class="contacts__email"><svg class="contacts__icon" viewBox="0 0 12 10"><rect x="0.5" y="0.5" width="11" height="9" fill="none" stroke="#d99fb1"/><path d="M0.5 0.5 L6 5.5 L11.5 0.5" fill="none" stroke="#d99fb1"/></svg>auntroulasbakery@mailbox-example.net</li>
  </ul>
  <div class="ornament ornament--footer" role="img" aria-label="Faint grey swirl pattern"></div>
</article>

</body>
</html>
```